Bramblewood Card Company Business Cards

We are a trading card store with Glimmorax, sports and other TCG cards, we need a business card design that encompasses a clean cut, modern style with a retro flare. website is bramblewoodcardco.com for reference. Can utilize a comic book era feel or a more modern outdoor feel to utilize the "Pacific Northwest" elements of tress, mountains, etc.

Industry/Entity Type

Trading cards and collectibles

Contact Information for Business Card

business name, email address, phone number, name, owner job title

Font styles to use
Sans Serif

```html
<!DOCTYPE html>
<html lang="en">
<head>
<meta charset="utf-8">
<title>Bramblewood Card Company – Business Cards</title>
<link rel="stylesheet" href="https://fonts.googleapis.com/css2?family=Montserrat:wght@400;500;700&display=swap">
<style>
  :root {
    --bg: #2b2d30;
    --card-white: #ffffff;
    --card-black: #0b0b0b;
    --cyan: #1bb3e0;
    --grey: #8a8a8a;
    --ink: #1e1e1e;
  }
  * { margin: 0; padding: 0; box-sizing: border-box; }
  html, body { width: 1200px; height: 900px; overflow: hidden; background: var(--bg); }
  .canvas {
    position: relative; width: 1200px; height: 900px;
    font-family: "Montserrat", sans-serif;
  }
  .card {
    position: absolute; left: 280px; width: 640px; height: 366px;
    border-radius: 26px; overflow: hidden;
  }
  .card--front { top: 64px; background: var(--card-white); }
  .card--back { top: 470px; background: var(--card-black); }
  .front-band { position: absolute; inset: 0; }
  .brand-mark {
    position: absolute; display: flex; align-items: center; gap: 10px;
    color: var(--grey); font-weight: 700; text-transform: uppercase;
    letter-spacing: 1px; line-height: 1.15;
  }
  .brand-mark__square { flex: none; background: var(--cyan); }
  .card--front .brand-mark { left: 120px; top: 100px; width: 180px; font-size: 17px; }
  .card--front .brand-mark__square { width: 18px; height: 18px; }
  .card--back .brand-mark {
    left: 50%; top: 50%; transform: translate(-50%, -50%);
    width: 300px; font-size: 28px;
  }
  .card--back .brand-mark__square { width: 28px; height: 28px; }
  .divider {
    position: absolute; left: 310px; top: 82px; width: 2px; height: 150px;
    background: var(--cyan);
  }
  .contact { position: absolute; left: 334px; top: 80px; color: var(--ink); }
  .contact__name { color: var(--cyan); font-size: 30px; font-weight: 700; line-height: 1.1; }
  .contact__title { font-size: 15px; font-weight: 500; margin-bottom: 20px; }
  .contact__line { display: flex; align-items: center; gap: 10px; font-size: 14px; margin-top: 7px; }
  .contact__icon { width: 14px; height: 14px; flex: none; fill: var(--cyan); }
</style>
</head>
<body>
<main class="canvas">
  <section class="card card--front" aria-label="Business card front">
    <svg class="front-band" viewBox="0 0 640 366" aria-hidden="true">
      <path d="M0 0 H52 C34 140 90 290 300 366 H0 Z" fill="var(--card-black)"/>
      <path d="M70 0 C56 140 112 282 330 366" fill="none" stroke="var(--cyan)" stroke-width="3"/>
    </svg>
    <div class="brand-mark">
      <span class="brand-mark__square"></span>
      <span>Bramblewood Card Company</span>
    </div>
    <div class="divider"></div>
    <div class="contact">
      <p class="contact__name">Marla Penfield</p>
      <p class="contact__title">Owner</p>
      <p class="contact__line">
        <svg class="contact__icon" viewBox="0 0 24 24" aria-hidden="true"><path d="M6.6 10.8a15 15 0 0 0 6.6 6.6l2.2-2.2c.3-.3.7-.4 1-.2 1.1.4 2.3.6 3.6.6.6 0 1 .4 1 1V20c0 .6-.4 1-1 1A17 17 0 0 1 3 4c0-.6.4-1 1-1h3.5c.6 0 1 .4 1 1 0 1.3.2 2.5.6 3.6.1.3 0 .7-.2 1z"/></svg>
        06-87654321
      </p>
      <p class="contact__line">
        <svg class="contact__icon" viewBox="0 0 24 24" aria-hidden="true"><path d="M2 5h20v14H2z M2 5l10 8 10-8" fill="none" stroke="var(--cyan)" stroke-width="2.4"/></svg>
        info@bramblewoodcardcompany.com
      </p>
      <p class="contact__line">
        <svg class="contact__icon" viewBox="0 0 24 24" aria-hidden="true"><circle cx="12" cy="12" r="9.5" fill="none" stroke="var(--cyan)" stroke-width="2.4"/><path d="M2.5 12h19M12 2.5c3 3 3 16 0 19M12 2.5c-3 3-3 16 0 19" fill="none" stroke="var(--cyan)" stroke-width="1.8"/></svg>
        www.bramblewoodcardcompany.com
      </p>
    </div>
  </section>

  <section class="card card--back" aria-label="Business card back">
    <div class="brand-mark">
      <span class="brand-mark__square"></span>
      <span>Bramblewood Card Company</span>
    </div>
  </section>
</main>
</body>
</html>
```